Carving New Ground: A Handbook for Builders

I need a book cover. The genre is self-help. would like something that looks original. The book is a barber's story. A barber who earns an M.B.A. I don't mind some type of scissor but I do not want it held to a cosmetology market. Something that speaks to everyone. No stock images. Format 4.25" x 7" This is what book printers call a pocket book.

• Original cover. No stock images.
• I like scissors. Maybe stick men. Creativity
• No Stock Images. No Clippers

```html
<!DOCTYPE html>
<html lang="en">
<head>
<meta charset="utf-8">
<title>Carving New Ground – Book Cover</title>
<link rel="stylesheet" href="https://fonts.googleapis.com/css2?family=Fira+Sans+Condensed:wght@800&family=Open+Sans:wght@600;700&display=swap">
<style>
  :root {
    --stage: #ececec;
    --cover: #161616;
    --frame: #8a8a8a;
    --title-red: #e3141b;
    --text-white: #ffffff;
    --art-red: #c8161d;
    --art-gold: #e8a21c;
  }
  * { margin: 0; padding: 0; box-sizing: border-box; }
  html, body {
    width: 1200px;
    height: 800px;
    overflow: hidden;
    background: var(--stage);
  }
  .stage {
    position: relative;
    width: 1200px;
    height: 800px;
  }
  .cover {
    position: absolute;
    left: 355px;
    top: 40px;
    width: 490px;
    height: 720px;
    background: var(--cover);
  }
  .cover-frame {
    position: absolute;
    inset: 15px;
    border: 4px solid var(--frame);
  }
  .art-scissors {
    position: absolute;
    left: 107px;
    top: 80px;
    width: 205px;
    height: 107px;
    background: linear-gradient(150deg, var(--art-red) 0%, var(--art-red) 55%, var(--art-gold) 100%);
    border-radius: 6px;
  }
  .title {
    position: absolute;
    left: 0;
    right: 0;
    top: 198px;
    text-align: center;
    font-family: "Fira Sans Condensed", sans-serif;
    font-weight: 800;
    color: var(--title-red);
  }
  .title-main {
    display: block;
    font-size: 68px;
    line-height: 64px;
    letter-spacing: 1px;
  }
  .title-second {
    display: block;
    font-size: 50px;
    line-height: 48px;
    letter-spacing: 0.5px;
  }
  .subtitle {
    position: absolute;
    left: 0;
    right: 0;
    top: 312px;
    text-align: center;
    font-family: "Open Sans", sans-serif;
    font-weight: 700;
    font-size: 25px;
    line-height: 30px;
    color: var(--text-white);
  }
  .art-figure {
    position: absolute;
    left: 141px;
    top: 367px;
    width: 229px;
    height: 233px;
    background: linear-gradient(135deg, #2a1a1a 0%, #3a1416 100%);
    border: 4px solid var(--art-red);
  }
  .tagline {
    position: absolute;
    left: 0;
    right: 0;
    top: 642px;
    text-align: center;
    font-family: "Open Sans", sans-serif;
    font-weight: 600;
    font-size: 16px;
    line-height: 22px;
    color: var(--text-white);
    word-spacing: 1px;
  }
  .tagline .dot { margin: 0 12px; }
</style>
</head>
<body>
  <main class="stage">
    <section class="cover">
      <div class="cover-frame"></div>
      <div class="art-scissors" role="img" aria-label="Illustration of open red and gold scissors"></div>
      <h1 class="title">
        <span class="title-main">CARVING</span>
        <span class="title-second">NEW GROUND</span>
      </h1>
      <p class="subtitle">A HANDBOOK FOR BUILDERS</p>
      <div class="art-figure" role="img" aria-label="Line drawing of a stick figure holding scissors, cutting through a red frame"></div>
      <p class="tagline"><span class="dot">•</span>A barber who earns an M.B.A<span class="dot">•</span></p>
    </section>
  </main>
</body>
</html>
```